List Now, Launch Later - DL Flyer front & back

Looking for a flyer that has nothing much other than “List Now, Launch Later” on the front with text to fill the back. With image on front that symbolises launch, maybe house being launch like a rocket.
The text has yet to be written but here is the gist: This is for the back of flyer.
List property and delay the launch. In the meantime, we can:
· Prepare contract
· Prepare marketing
· Prepare the property
· Do the Pest and Building Report
· Give the tenants their due notice of sale
· Advise buyers in an off market capacity
This ensures we are first to market when the time comes rather than coming onto the market along with a surge of spring sellers. Buyers are still buying now. The lack of stock is inadvertently creating strength in the market.
The feel has to be modern, clean, contemporary & graphic

```html
<!DOCTYPE html>
<html lang="en">
<head>
<meta charset="utf-8">
<title>List Now, Launch Later – Flyer Front</title>
<link href="https://fonts.googleapis.com/css2?family=Montserrat:wght@800&display=swap" rel="stylesheet">
<style>
  :root {
    --brand-purple: #3b3a9c;
    --brand-orange: #f7a823;
    --photo-white: #f6f5f3;
    --photo-grey: #cfccc8;
    --photo-shadow: #a9a6a2;
    --photo-wood: #b89a7c;
    --band-grey: rgba(120, 118, 126, 0.28);
  }
  html, body {
    margin: 0;
    padding: 0;
    overflow: hidden;
    background: #ffffff;
  }
  .flyer {
    position: relative;
    width: 849px;
    height: 1200px;
    overflow: hidden;
    font-family: "Montserrat", sans-serif;
  }
  .interior-photo {
    position: absolute;
    inset: 0;
    background:
      radial-gradient(ellipse 420px 260px at 120px 1130px, rgba(184,154,124,0.85) 0%, rgba(184,154,124,0) 100%),
      radial-gradient(ellipse 360px 300px at 560px 620px, rgba(169,166,162,0.55) 0%, rgba(169,166,162,0) 100%),
      linear-gradient(90deg, rgba(255,255,255,0) 0%, rgba(255,255,255,0.35) 55%, rgba(210,208,205,0.35) 100%),
      linear-gradient(180deg, var(--photo-white) 0%, var(--photo-white) 38%, #e4e2df 50%, var(--photo-grey) 60%, #e8e6e3 72%, #eeebe7 84%, var(--photo-wood) 100%);
  }
  .interior-veil {
    position: absolute;
    inset: 0;
    background: linear-gradient(180deg, rgba(255,255,255,0.45) 0%, rgba(255,255,255,0.25) 100%);
  }
  .launch-mark {
    position: absolute;
    left: 175px;
    top: 88px;
    width: 272px;
    height: 356px;
    border-radius: 46% 46% 40% 40%;
    background:
      radial-gradient(circle at 30% 82%, rgba(247,168,35,0.75) 0%, rgba(247,168,35,0) 38%),
      linear-gradient(160deg, rgba(59,58,156,0.62) 0%, rgba(59,58,156,0.45) 70%, rgba(59,58,156,0.3) 100%);
  }
  .arrow-band {
    position: absolute;
    left: 160px;
    top: 902px;
    width: 689px;
    height: 72px;
    background: var(--band-grey);
  }
  .accent-rule {
    position: absolute;
    left: 175px;
    top: 694px;
    width: 170px;
    height: 6px;
    background: var(--brand-orange);
  }
  .headline {
    position: absolute;
    left: 170px;
    top: 754px;
    margin: 0;
    font-weight: 800;
    font-size: 68px;
    line-height: 78px;
    letter-spacing: 3px;
    color: var(--brand-purple);
    text-transform: uppercase;
  }
  .next-arrow {
    position: absolute;
    left: 758px;
    top: 907px;
  }
</style>
</head>
<body>
  <main class="flyer">
    <div class="interior-photo" role="img" aria-label="Bright, modern white living room with grey sofa, fireplace and timber floor"></div>
    <div class="interior-veil"></div>

    <div class="launch-mark" role="img" aria-label="House-shaped rocket taking off with an orange flame"></div>

    <div class="arrow-band"></div>
    <div class="accent-rule"></div>
    <h1 class="headline">List now,<br>launch<br>later.</h1>

    <svg class="next-arrow" width="38" height="62" viewBox="0 0 38 62" aria-hidden="true">
      <polygon points="0,0 38,31 0,62" fill="var(--brand-orange)"/>
    </svg>
  </main>
</body>
</html>
```